PlayTallyCollective - Game Statistics and Achievement Tracking

I need a new modern design for an existing website.

The website is a project to track statistics and achievements for games (currently Vaporn Achievements/Stats and stats for Cargo Haul Odyssey 2 and Frontier Rig Journeys).
I am currently expanding the site with other platforms (like QVR) and more games.
I am also adding a user registration/signin with user profiles to show off their achievements and stats across all platforms and games.

The current website is available at https://plytly.example/
To search for data you can use the username "pixelornin" (without quotes).

The design should be modern and extendable and contain space for a logo.

The logo should match the project. It should combine Gaming with statistics.

Target Market(s)

Video game players

Number of Pages Required

5+ page

Font styles to use
Sans Serif

Requirements
Must have
• Basic Layout, User profile page (not yet available on live site), Search Page for Platforms/Games, Platform profile page, Dark theme

```html
<!DOCTYPE html>
<html lang="en">
<head>
<meta charset="utf-8">
<title>Search Haulvanta User – plytly.example</title>
<link rel="stylesheet" href="https://fonts.googleapis.com/css2?family=Outfit:wght@400;500;600;700&display=swap">
<style>
:root{
  --bg:#0f0f14;
  --text:#ffffff;
  --muted:#9a9ca6;
  --field:#1c1c22;
  --field-border:#3a3b44;
  --accent-a:#1f4fe8;
  --accent-b:#18c8f6;
  --scene-sky:#1f2735;
  --scene-dusk:#4a3a48;
  --scene-road:#3b3226;
}
*{box-sizing:border-box;margin:0;padding:0}
html,body{width:1200px;height:736px;overflow:hidden;background:var(--bg)}
body{font-family:"Outfit",sans-serif;color:var(--text);position:relative}
.hero-scene{
  position:absolute;left:0;top:170px;width:1200px;height:520px;
  background:
    radial-gradient(ellipse 62% 58% at 50% 55%, transparent 40%, var(--bg) 100%),
    linear-gradient(180deg, var(--scene-sky) 0%, #2b3347 28%, var(--scene-dusk) 42%, #2a2724 58%, var(--scene-road) 75%, var(--bg) 100%);
}
.site-header{position:absolute;left:94px;right:94px;top:18px;height:40px;display:flex;align-items:center;justify-content:space-between}
.brand{display:flex;align-items:center;gap:10px;font-size:22px;font-weight:700;letter-spacing:.2px}
.brand-mark{width:26px;height:26px;border-radius:6px;background:var(--accent-b)}
.main-nav{display:flex;align-items:center;gap:18px;font-size:11.5px;color:var(--muted);margin-top:-6px}
.nav-item{display:flex;align-items:center;gap:5px;position:relative}
.nav-item svg{width:10px;height:10px}
.nav-item.is-active{color:var(--text);font-weight:500}
.nav-item.is-active::after{content:"";position:absolute;left:5px;bottom:-9px;width:3px;height:3px;border-radius:50%;background:var(--text)}
.caret{width:7px;height:7px}
.search-hero{position:absolute;left:0;right:0;top:180px;text-align:center}
.search-title{font-size:45px;font-weight:600;letter-spacing:-.3px;line-height:56px}
.search-form{position:absolute;left:236px;top:73px;width:730px;height:51px;border-radius:26px;background:var(--field);border:1px solid var(--field-border);display:flex;align-items:center}
.field-icon{width:18px;height:20px;margin-left:20px}
.field-label{margin-left:14px;font-size:15px;font-weight:500}
.search-button{position:absolute;right:-1px;top:-1px;height:51px;width:134px;border-radius:26px;border:0;background:linear-gradient(90deg,var(--accent-a),var(--accent-b));color:var(--text);font:500 14px "Outfit",sans-serif;display:flex;align-items:center;justify-content:center;gap:12px}
.search-button .dot{width:18px;height:18px;border-radius:50%;background:#fff;position:relative}
.search-button .dot::after{content:"";position:absolute;right:-3px;bottom:-3px;width:5px;height:5px;border-radius:50%;background:#fff}
.site-footer{position:absolute;left:94px;right:94px;top:696px;display:flex;justify-content:space-between;font-size:12.5px}
</style>
</head>
<body>
<div class="hero-scene" role="img" aria-label="Night-time city boulevard from a racing game with casino towers, traffic lights and cars"></div>

<header class="site-header">
  <div class="brand"><span class="brand-mark"></span>plytly.example</div>
  <nav class="main-nav">
    <span class="nav-item"><svg viewBox="0 0 10 10"><path d="M1 5 5 1l4 4v4H6V6H4v3H1z" fill="currentColor"/></svg>Home</span>
    <span class="nav-item"><svg viewBox="0 0 10 10"><circle cx="5" cy="5" r="4.5" fill="currentColor"/></svg>Vaporn<svg class="caret" viewBox="0 0 8 8"><path d="M1 2.5 4 5.5 7 2.5" stroke="currentColor" fill="none"/></svg></span>
    <span class="nav-item is-active"><svg viewBox="0 0 10 10"><rect x="0.5" y="2.5" width="9" height="5" rx="2.5" fill="currentColor"/></svg>Game<svg class="caret" viewBox="0 0 8 8"><path d="M1 2.5 4 5.5 7 2.5" stroke="currentColor" fill="none"/></svg></span>
    <span class="nav-item"><svg viewBox="0 0 10 10"><circle cx="5" cy="5" r="4.5" fill="currentColor"/><rect x="4.4" y="4" width="1.2" height="4" fill="#0f0f14"/><circle cx="5" cy="2.7" r=".7" fill="#0f0f14"/></svg>About Us<svg class="caret" viewBox="0 0 8 8"><path d="M1 2.5 4 5.5 7 2.5" stroke="currentColor" fill="none"/></svg></span>
  </nav>
</header>

<main class="search-hero">
  <h1 class="search-title">Search Haulvanta User</h1>
  <form class="search-form">
    <svg class="field-icon" viewBox="0 0 18 20"><circle cx="9" cy="6" r="4.2" stroke="#fff" stroke-width="1.4" fill="none"/><path d="M1.5 19c0-4.5 3.3-7 7.5-7s7.5 2.5 7.5 7" stroke="#fff" stroke-width="1.4" fill="none"/></svg>
    <span class="field-label">User Name</span>
    <button class="search-button" type="button"><span class="dot"></span>Search</button>
  </form>
</main>

<footer class="site-footer">
  <span>© Haulvanta.example</span>
  <span>Imprint</span>
</footer>
</body>
</html>
```